****Modern, Urban & Professional Business card for electrical company (electrician

Require a business card for an electrical company providing electrician services. Specifically residential and commercial property.

Business card must represent the company and brand and use the company colours in some way whether that be just the logo & name or full colour. Would like icons to be used for social media platforms email and telephone. Open to use of QR code but don’t want the card to look too busy.
QR Code must link to contact details on phone. Add contact with Name, Company, Phone Number, Website on phone contact details.

If you are a designer working on this job we would appreciate if you could follow our social media channels in exchange for a follow back. As a small start up business every like/follow helps :)

Would like to make the business card into a magnet (single sided also) future project

Industry/Entity Type

Electrician

Contact Information for Business Card

Colours to include but not limited to
dark blue -142455
sky blue - 0094da

91 x 55 mm size

Information to include:

Reid Calloway
Director
0215567391

www.brightwirepower.co.nz
info@brightwirepower.co.nz
www.Facebook.com/brightwirepower
www.instagram.com/brightwire.power

Might be good to add:
24 hour emergency service

Requirements
Must have
• Email address included on card

```html
<!DOCTYPE html>
<html lang="en">
<head>
<meta charset="utf-8">
<title>Brightwire Power – Business Card</title>
<link rel="stylesheet" href="https://fonts.googleapis.com/css2?family=Roboto:wght@400;700&display=swap">
<style>
  :root {
    --navy: #1d2353;
    --band-navy: #0f2a4d;
    --sky: #2293d3;
    --ink: #1a1f3d;
    --white: #ffffff;
    --backdrop: #e8e5e0;
    --facebook-dot: #3b5b9a;
    --instagram-dot: #8a4a55;
  }
  * { box-sizing: border-box; margin: 0; padding: 0; }
  html, body {
    width: 900px; height: 1200px; overflow: hidden;
    background: var(--backdrop);
    font-family: "Roboto", Arial, sans-serif;
  }
  .canvas { position: relative; width: 900px; height: 1200px; }

  .card {
    position: absolute; left: 76px; width: 747px; height: 451px;
    box-shadow: 0 3px 8px rgba(0,0,0,.25);
    overflow: hidden;
  }
  .card--front { top: 117px; background: var(--white); }
  .card--back  { top: 625px; background: var(--sky); }

  .brand { position: absolute; display: flex; align-items: center; }
  .brand__dot { border-radius: 50%; background: var(--navy); flex: none; }
  .brand__name { font-weight: 700; line-height: 1.02; letter-spacing: .5px; }

  .card--front .brand { left: 72px; top: 74px; }
  .card--front .brand__dot { width: 97px; height: 97px; margin-right: 6px; }
  .card--front .brand__name { font-size: 32px; color: var(--sky); }

  .card--back .brand { left: 135px; top: 150px; }
  .card--back .brand__dot { width: 151px; height: 151px; margin-right: 12px; }
  .card--back .brand__name { font-size: 52px; color: var(--navy); }

  .person { position: absolute; left: 175px; top: 197px; color: var(--ink); }
  .person__name { font-size: 30px; font-weight: 700; line-height: 1; color: var(--ink); }
  .person__surname { color: var(--sky); }
  .person__role { font-size: 20px; letter-spacing: .8px; margin-top: 2px; }

  .contact { position: absolute; left: 175px; top: 284px; list-style: none; }
  .contact__item {
    display: flex; align-items: center; height: 24px;
    font-size: 21px; letter-spacing: 1px; color: var(--ink);
  }
  .contact__icon { width: 16px; height: 16px; margin-right: 12px; flex: none; }

  .band { position: absolute; top: 378px; height: 27px; }
  .band--accent { left: 0; width: 167px; background: var(--sky); }
  .band--service {
    left: 175px; right: 0; background: var(--band-navy);
    color: var(--white); font-size: 21px; letter-spacing: 1.2px;
    padding-left: 28px; line-height: 27px;
  }

  .social { position: absolute; top: 381px; display: flex; align-items: center; }
  .social--facebook { left: 135px; }
  .social--instagram { left: 388px; }
  .social__dot { width: 26px; height: 26px; border-radius: 50%; margin-right: 11px; }
  .social--facebook .social__dot { background: var(--facebook-dot); }
  .social--instagram .social__dot { background: var(--instagram-dot); }
  .social__handle { font-size: 22px; letter-spacing: 1.2px; color: var(--white); }
</style>
</head>
<body>
<main class="canvas">

  <section class="card card--front">
    <div class="brand">
      <span class="brand__dot"></span>
      <span class="brand__name">BRIGHTWIRE<br>POWER</span>
    </div>

    <div class="person">
      <h1 class="person__name">REID <span class="person__surname">CALLOWAY</span></h1>
      <p class="person__role">Director</p>
    </div>

    <ul class="contact">
      <li class="contact__item">
        <svg class="contact__icon" viewBox="0 0 16 16" aria-hidden="true">
          <path d="M3 1.5l2.5 0 1.2 3-1.6 1.2c.8 1.8 2.2 3.2 4 4l1.2-1.6 3 1.2v2.5c0 .8-.7 1.4-1.5 1.3C6.4 12.6 2.4 8.6 1.6 3 1.5 2.2 2.2 1.5 3 1.5z" fill="var(--sky)"/>
          <path d="M9.5 2.5a4 4 0 0 1 4 4M9.5 5a1.5 1.5 0 0 1 1.5 1.5" stroke="var(--sky)" stroke-width="1.3" fill="none"/>
        </svg>
        0215567391
      </li>
      <li class="contact__item">
        <svg class="contact__icon" viewBox="0 0 16 16" aria-hidden="true">
          <rect x="1.5" y="3.5" width="13" height="9" rx="1" fill="none" stroke="var(--sky)" stroke-width="1.5"/>
          <path d="M2 4.5l6 4.5 6-4.5" fill="none" stroke="var(--sky)" stroke-width="1.5"/>
        </svg>
        info@brightwirepower.co.nz
      </li>
      <li class="contact__item">
        <svg class="contact__icon" viewBox="0 0 16 16" aria-hidden="true">
          <circle cx="8" cy="8" r="6.5" fill="var(--sky)"/>
          <path d="M1.5 8h13M8 1.5c2.2 2 2.2 11 0 13M8 1.5c-2.2 2-2.2 11 0 13" stroke="var(--white)" stroke-width="1" fill="none"/>
        </svg>
        www.brightwirepower.co.nz
      </li>
    </ul>

    <div class="band band--accent"></div>
    <div class="band band--service">24 hour emergency service</div>
  </section>

  <section class="card card--back">
    <div class="brand">
      <span class="brand__dot"></span>
      <span class="brand__name">BRIGHTWIRE<br>POWER</span>
    </div>

    <div class="social social--facebook">
      <span class="social__dot"></span>
      <span class="social__handle">brightwirepower</span>
    </div>
    <div class="social social--instagram">
      <span class="social__dot"></span>
      <span class="social__handle">brightwire.power</span>
    </div>
  </section>

</main>
</body>
</html>
```